Harbor Crestline (Business Card Design)

Need business cards designed. Something modern, chic, and sleek. Mabye the back of the card should be the navy blue that is in the logo and then just the logo on the back.

Target Market(s)

Those in the hotel, office, and renovation industry

Contact Information for Business Card

1. Logo 2. Dorian Fenwick 3. CEO/Founder 4. Phone: (833) HarbCre / (833) 427-2731 5. Email: dorian@theharborcrestline.com 6. Website: www.theharborcrestline.com

Font styles to use
Other font styles liked:
• Look at the logo font and base the font for everything else off of that.

Colors
0054AA
0677BA
7BADD7
CADEEF
E8F1F8

Requirements
Must have
• Colors that are associated in the logo
Nice to have
• Sleek modern clean and chic design.

```html
<!DOCTYPE html>
<html lang="en">
<head>
<meta charset="utf-8">
<title>Harbor Crestline — Business Card</title>
<link rel="stylesheet" href="https://fonts.googleapis.com/css2?family=Open+Sans:wght@400;600;700&display=swap">
<style>
  :root {
    --navy: #0c1a4b;
    --gold: #c49a3f;
    --paper: #f5f5f5;
    --ink: #161616;
    --faint: #e2e1e6;
    --stage: #2a2a2c;
  }
  * { box-sizing: border-box; margin: 0; padding: 0; }
  html, body { width: 1200px; height: 780px; overflow: hidden; }
  body {
    background: var(--stage);
    font-family: "Open Sans", Arial, sans-serif;
    position: relative;
  }
  .card {
    position: absolute;
    top: 235px;
    width: 540px;
    height: 309px;
    overflow: hidden;
    box-shadow: 0 10px 30px rgba(0,0,0,.45);
  }
  /* Front */
  .card-front { left: 30px; background: var(--paper); color: var(--ink); }
  .front-wordmark {
    position: absolute; left: 34px; top: 34px;
    display: flex; align-items: center; gap: 10px;
  }
  .wordmark-square { width: 12px; height: 12px; background: var(--gold); }
  .wordmark-name {
    font-weight: 700; font-size: 21px; letter-spacing: 2px;
    text-transform: uppercase; color: var(--navy);
  }
  .faint-square {
    position: absolute; left: 300px; top: 120px;
    width: 150px; height: 150px; background: var(--faint);
  }
  .divider {
    position: absolute; left: 30px; right: 58px; top: 152px;
    height: 1.5px; background: var(--ink);
  }
  .holder {
    position: absolute; right: 64px; top: 86px; text-align: right;
  }
  .holder-name { font-weight: 700; font-size: 30px; line-height: 1.1; }
  .holder-first { color: var(--gold); }
  .holder-title { font-size: 15px; margin-top: 2px; }
  .gold-band {
    position: absolute; right: 24px; top: 148px;
    width: 28px; height: 62px; background: var(--gold);
  }
  .contact {
    position: absolute; left: 34px; top: 168px;
    font-size: 13px; line-height: 1.5;
  }
  .contact-address { margin-bottom: 4px; }
  .contact-line { display: flex; align-items: center; gap: 7px; }
  .contact-line svg { width: 11px; height: 11px; flex: none; }
  /* Back */
  .card-back {
    left: 630px; background: var(--navy);
    display: flex; align-items: center; justify-content: center; gap: 14px;
  }
  .back-square { width: 16px; height: 16px; background: var(--gold); }
  .back-name {
    color: #fff; font-weight: 700; font-size: 30px;
    letter-spacing: 3px; text-transform: uppercase;
  }
</style>
</head>
<body>
  <section class="card card-front" aria-label="Business card front">
    <div class="front-wordmark">
      <span class="wordmark-square"></span>
      <span class="wordmark-name">Harbor Crestline</span>
    </div>
    <div class="faint-square"></div>
    <div class="holder">
      <p class="holder-name"><span class="holder-first">Dorian</span> Fenwick</p>
      <p class="holder-title">CEO/Founder</p>
    </div>
    <div class="divider"></div>
    <div class="gold-band"></div>
    <div class="contact">
      <p class="contact-address">4120 Marlow Ridge Rd<br>Suite 210, Easton, MD 21601</p>
      <p class="contact-line">
        <svg viewBox="0 0 12 12"><path fill="var(--gold)" d="M2.5 1l2 2.2-1 1.3a7 7 0 0 0 4 4l1.3-1 2.2 2-1.2 1.5C5.6 11 1 6.4 1 2.2z"/></svg>
        (833) HarbCre / (833) 427-2731
      </p>
      <p class="contact-line">
        <svg viewBox="0 0 12 12"><circle cx="6" cy="6" r="5" fill="none" stroke="var(--gold)" stroke-width="1.3"/><path d="M1 6h10M6 1c-2.5 3-2.5 7 0 10M6 1c2.5 3 2.5 7 0 10" fill="none" stroke="var(--gold)" stroke-width="1"/></svg>
        www.theharborcrestline.com
      </p>
      <p class="contact-line">
        <svg viewBox="0 0 12 12"><rect x="1" y="2.5" width="10" height="7" fill="none" stroke="var(--gold)" stroke-width="1.3"/><path d="M1 2.5l5 4 5-4" fill="none" stroke="var(--gold)" stroke-width="1.2"/></svg>
        dorian@theharborcrestline.com
      </p>
    </div>
  </section>

  <section class="card card-back" aria-label="Business card back">
    <span class="back-square"></span>
    <span class="back-name">Harbor Crestline</span>
  </section>
</body>
</html>
```